Quillbrook IT company focused on 3 areas of IT

Looking for something similar to attached cards. Logo for quillbrook also attached.. Looking for something clean as far as colors (surprise me).. Quill stands for 3 primary areas, web design, consulting and network infrastructure design. Please email me if you have any questions. Looking forward to seeing how creative and professional this card will look. Thank you,

Target Market(s)

Small business/consumers looking for It services

Industry/Entity Type

It Service

Contact Information for Business Card

Dorin Vasek
Principal Consultant

202-555-0173

www.quillbrook-example.com
dvasek@quillbrook-example.com

27416 Copper Lantern Way,
Germantown, MD 20999

Colors

Designer to choose colors to be used in the design.

Requirements
Must have
• attached Logo design. Feel free to play with the colors.. If you have a better idea for a card, please fee free to send me. Looking for something clean/modern. Should have tech feel, not cheesy.
Nice to have
• Surprise me :-)..

```html
<!DOCTYPE html>
<html lang="en">
<head>
<meta charset="utf-8">
<title>Quillbrook Business Card</title>
<link href="https://fonts.googleapis.com/css2?family=Lato:wght@300;400;700;900&display=swap" rel="stylesheet">
<style>
  :root {
    --ink: #1d2a2b;
    --paper: #ffffff;
    --stage: #e4e7e7;
    --text-dark: #2a3233;
    --text-mid: #4a5354;
    --icon-bg: #3c4546;
  }
  * { box-sizing: border-box; margin: 0; padding: 0; }
  html, body {
    width: 1200px; height: 900px; overflow: hidden;
    background: var(--stage);
    font-family: "Lato", sans-serif;
  }
  .canvas { position: relative; width: 1200px; height: 900px; }

  .card {
    position: absolute;
    width: 560px; height: 320px;
    border-radius: 18px;
    overflow: hidden;
    box-shadow: 0 10px 30px rgba(0,0,0,0.18);
  }

  /* Logo side */
  .card--brand {
    left: 120px; top: 110px;
    background: var(--ink);
    display: flex; flex-direction: column; align-items: center; justify-content: center;
    color: var(--paper);
  }
  .brand-name {
    display: flex; align-items: center; gap: 14px;
    font-weight: 900; font-size: 44px; letter-spacing: 3px;
  }
  .brand-mark { width: 22px; height: 22px; background: var(--paper); }
  .brand-url {
    margin-top: 70px;
    font-weight: 700; font-size: 14px; letter-spacing: 4px;
  }

  /* Contact side */
  .card--contact {
    left: 520px; top: 470px;
    background: var(--paper);
  }
  .contact-band { position: absolute; inset: 0; }
  .contact-band svg { width: 100%; height: 100%; display: block; }
  .band-brand {
    position: absolute; right: 30px; top: 50px;
    display: flex; align-items: center; gap: 10px;
    color: var(--paper); font-weight: 900; font-size: 26px; letter-spacing: 2px;
  }
  .band-brand .brand-mark { width: 14px; height: 14px; }

  .person { position: absolute; left: 40px; top: 92px; color: var(--text-dark); }
  .person-name { font-size: 18px; font-weight: 300; letter-spacing: 0.5px; }
  .person-name strong { font-weight: 700; }
  .person-title { font-size: 11px; color: var(--text-mid); margin-top: 2px; }

  .contact-list { position: absolute; left: 40px; top: 170px; list-style: none; }
  .contact-item {
    display: flex; align-items: center; gap: 10px;
    font-size: 12px; color: var(--text-dark);
    margin-bottom: 8px; line-height: 1.2;
  }
  .contact-icon {
    width: 22px; height: 22px; border-radius: 50%;
    background: var(--icon-bg);
    display: flex; align-items: center; justify-content: center; flex: none;
  }
  .contact-icon svg { width: 12px; height: 12px; }
</style>
</head>
<body>
<main class="canvas">

  <section class="card card--brand" aria-label="Card front">
    <div class="brand-name"><span class="brand-mark"></span>QUILLBROOK</div>
    <div class="brand-url">www.quillbrook-example.com</div>
  </section>

  <section class="card card--contact" aria-label="Card back">
    <div class="contact-band">
      <svg viewBox="0 0 560 320" preserveAspectRatio="none">
        <polygon points="110,0 560,0 560,210" fill="var(--ink)" />
      </svg>
    </div>
    <div class="band-brand"><span class="brand-mark"></span>QUILLBROOK</div>

    <div class="person">
      <p class="person-name">DORIN <strong>VASEK</strong></p>
      <p class="person-title">Principal Consultant</p>
    </div>

    <ul class="contact-list">
      <li class="contact-item">
        <span class="contact-icon"><svg viewBox="0 0 12 12"><rect x="3.5" y="1" width="5" height="10" rx="1" fill="none" stroke="#fff" stroke-width="1.2"/><circle cx="6" cy="9" r="0.7" fill="#fff"/></svg></span>
        202-555-0173
      </li>
      <li class="contact-item">
        <span class="contact-icon"><svg viewBox="0 0 12 12"><rect x="1" y="3" width="10" height="7" fill="none" stroke="#fff" stroke-width="1.1"/><polyline points="1,3 6,7 11,3" fill="none" stroke="#fff" stroke-width="1.1"/></svg></span>
        dvasek@quillbrook-example.com
      </li>
      <li class="contact-item">
        <span class="contact-icon"><svg viewBox="0 0 12 12"><circle cx="6" cy="6" r="4.8" fill="none" stroke="#fff" stroke-width="1.1"/><ellipse cx="6" cy="6" rx="2" ry="4.8" fill="none" stroke="#fff" stroke-width="1"/><line x1="1.2" y1="6" x2="10.8" y2="6" stroke="#fff" stroke-width="1"/></svg></span>
        www.quillbrook-example.com
      </li>
      <li class="contact-item">
        <span class="contact-icon"><svg viewBox="0 0 12 12"><path d="M6 11 C3 7 2.5 5.5 2.5 4.5 A3.5 3.5 0 0 1 9.5 4.5 C9.5 5.5 9 7 6 11Z" fill="#fff"/><circle cx="6" cy="4.5" r="1.2" fill="var(--icon-bg)"/></svg></span>
        <span>27416 Copper Lantern Way,<br>Germantown, MD 20999</span>
      </li>
    </ul>
  </section>

</main>
</body>
</html>
```